Road Construction Company needs business cards

We would like a new business card designed for our business.

We're a road construction company based in Qld, Australia.

Can the business card please have the following information on it.

Name: Warren Halbeck
Position: General Manager
Phone: 0472 915 348
Email: Warren.halbeck@tovrin.com.au
Address: 87 Marrow Ave, Pendlebay, QLD, 4023
Website: www.tovrin.com.au

Visually we'd like the card to be professional and simple.

Attached is our logo.

Our website is www.tovrin.com.au

Target Market(s)

Men aged 25-60

Contact Information for Business Card

As listed in project description

Font styles to use
Serif

Requirements
Must have
• Large logo on back of card

```html
<!DOCTYPE html>
<html lang="en">
<head>
<meta charset="utf-8">
<title>Tovrin Business Card</title>
<link href="https://fonts.googleapis.com/css2?family=Open+Sans:wght@400;600;800&display=swap" rel="stylesheet">
<style>
  :root {
    --stage: #2b2e34;
    --card-dark: #202125;
    --card-blue: #1254a6;
    --accent-blue: #3a9ad9;
    --text-light: #f2f4f6;
    --white: #ffffff;
  }
  * { margin: 0; padding: 0; box-sizing: border-box; }
  html, body {
    width: 1200px; height: 780px; overflow: hidden;
    background: var(--stage);
    font-family: "Open Sans", Arial, sans-serif;
  }
  .stage {
    position: relative; width: 1200px; height: 780px;
  }
  .card {
    position: absolute; top: 235px;
    width: 540px; height: 310px;
    border-radius: 24px;
    overflow: hidden;
    box-shadow: 0 18px 40px rgba(0,0,0,.45);
  }
  .card-front { left: 40px; background: var(--card-dark); }
  .card-back  { left: 620px; background: var(--card-blue); }

  .wordmark {
    font-weight: 800; color: var(--white); letter-spacing: 1px;
    line-height: 1;
  }
  .card-front .wordmark {
    position: absolute; left: 30px; top: 28px; font-size: 44px;
  }
  .card-back .wordmark {
    position: absolute; left: 0; right: 0; top: 50%;
    transform: translateY(-50%);
    text-align: center; font-size: 104px; letter-spacing: 3px;
  }

  .address {
    position: absolute; left: 30px; top: 98px;
    color: var(--text-light); font-size: 13px; line-height: 1.45;
  }
  .contact-list {
    position: absolute; left: 30px; top: 178px;
    list-style: none; color: var(--text-light); font-size: 13px; line-height: 1.55;
  }
  .contact-list li { display: flex; align-items: center; gap: 8px; }
  .contact-list svg { width: 12px; height: 12px; flex: none; fill: var(--accent-blue); }

  .person {
    position: absolute; right: 46px; top: 168px; text-align: right;
  }
  .person-name {
    color: var(--accent-blue); font-weight: 600; font-size: 30px; line-height: 1.1;
  }
  .person-title {
    color: var(--text-light); font-size: 16px; margin-top: 2px;
  }
  .edge-tab {
    position: absolute; right: 0; top: 172px;
    width: 22px; height: 56px; background: var(--white);
  }
</style>
</head>
<body>
<main class="stage">
  <section class="card card-front" aria-label="Business card front">
    <div class="wordmark">TOVRIN</div>
    <p class="address">87 Marrow Ave,<br>Pendlebay, QLD, 4023</p>
    <ul class="contact-list">
      <li><svg viewBox="0 0 24 24" aria-hidden="true"><path d="M6.6 10.8a15.1 15.1 0 0 0 6.6 6.6l2.2-2.2c.3-.3.7-.4 1-.2 1.1.4 2.3.6 3.6.6.6 0 1 .4 1 1V20c0 .6-.4 1-1 1A17 17 0 0 1 3 4c0-.6.4-1 1-1h3.5c.6 0 1 .4 1 1 0 1.3.2 2.5.6 3.6.1.3 0 .7-.2 1z"/></svg>0472 915 348</li>
      <li><svg viewBox="0 0 24 24" aria-hidden="true"><path d="M2 5h20v14H2zm2 2v.5l8 5 8-5V7l-8 5z"/></svg>www.tovrin.com.au</li>
      <li><svg viewBox="0 0 24 24" aria-hidden="true"><circle cx="12" cy="12" r="10"/></svg>Warren.halbeck@tovrin.com.au</li>
    </ul>
    <div class="person">
      <div class="person-name">Warren Halbeck</div>
      <div class="person-title">General Manager</div>
    </div>
    <div class="edge-tab"></div>
  </section>

  <section class="card card-back" aria-label="Business card back">
    <div class="wordmark">TOVRIN</div>
  </section>
</main>
</body>
</html>
```